Business Card Design

It's an investment advisory service for individuals with all there investment needs. Also financial consulting to businesses and governmental agencies on retirement plans etc. It's personalized not commoditized help. Should show strength, knowledge and money orientation.

Reason: Will be out of town setting up office.

Reason: waiting for the 2/3rds of group to vote

Reason: only half the votes are in, I'm calling and getting verbals, but at this time we are down to 2 designs.

Industry/Entity Type

Investment

Contact Information for Business Card

B. Rel K. Financial Consulting and Wealth Management, Berislav Mike Holcek, 5172 Pasadena Loma Verde, San Diego, CA 94417-6381, Registered Investment Advisor

Requirements
Nice to have
• Something money oriented

```html
<!DOCTYPE html>
<html lang="en">
<head>
<meta charset="utf-8">
<title>B. Rel K. Business Card</title>
<link href="https://fonts.googleapis.com/css2?family=Ubuntu:wght@400;500;700&display=swap" rel="stylesheet">
<style>
  :root {
    --backdrop: #e9e6e1;
    --card-white: #f7f7f5;
    --brand-green: #0b7a3b;
    --tag-grey: #6e6e6e;
    --on-green: #ffffff;
    --money-light: #eef1e4;
    --money-mid: #dfe6cf;
  }
  * { margin: 0; padding: 0; box-sizing: border-box; }
  html, body {
    width: 1200px; height: 1000px; overflow: hidden;
    background: var(--backdrop);
    font-family: "Ubuntu", sans-serif;
  }
  .business-card {
    position: absolute; left: 150px; top: 243px;
    width: 900px; height: 514px;
    display: flex;
    box-shadow: 0 6px 18px rgba(0,0,0,0.18);
  }
  .card-brand {
    position: relative; width: 441px; height: 100%;
    background: var(--card-white);
  }
  .money-visual {
    position: absolute; left: 300px; top: 160px; width: 141px; height: 270px;
    background: radial-gradient(ellipse at 70% 45%, var(--money-mid) 0%, var(--money-light) 50%, rgba(247,247,245,0) 80%);
  }
  .brand-mark {
    position: absolute; left: 0; right: 0; top: 180px;
    display: flex; align-items: center; justify-content: center; gap: 14px;
  }
  .brand-square {
    width: 34px; height: 34px; background: var(--brand-green);
  }
  .brand-name {
    font-weight: 700; font-size: 44px; color: var(--brand-green);
    letter-spacing: 0.5px;
  }
  .brand-tagline {
    position: absolute; left: 0; right: 0; top: 326px;
    text-align: center; color: var(--tag-grey);
    font-size: 24px; font-weight: 500; line-height: 32px;
  }
  .card-contact {
    flex: 1; height: 100%;
    background: var(--brand-green); color: var(--on-green);
    padding: 181px 0 0 61px;
  }
  .person-name { font-size: 29px; font-weight: 700; line-height: 34px; }
  .person-credentials { font-size: 17px; font-weight: 500; margin-top: 6px; }
  .person-credentials sup { font-size: 10px; }
  .person-title { font-size: 18px; font-weight: 500; margin-top: 7px; }
  .contact-list { list-style: none; margin-top: 22px; }
  .contact-list li { font-size: 21px; font-weight: 500; line-height: 31px; }
  .contact-list .email { margin-top: 6px; }
</style>
</head>
<body>
  <div class="business-card">
    <section class="card-brand">
      <div class="money-visual" role="img" aria-label="Faded photograph of stacked banknotes"></div>
      <div class="brand-mark">
        <span class="brand-square"></span>
        <span class="brand-name">B. Rel K.</span>
      </div>
      <p class="brand-tagline">Financial Consulting<br>and Wealth Management</p>
    </section>
    <section class="card-contact">
      <h1 class="person-name">Berislav "Mike" Holcek</h1>
      <p class="person-credentials">MBA, RP<sup>®</sup>, CRC<sup>®</sup></p>
      <p class="person-title">Registered Investment Advisor</p>
      <ul class="contact-list">
        <li>858-310-4718</li>
        <li>775-602-1935</li>
        <li class="email">mike.holcek@relkwealth.net</li>
      </ul>
    </section>
  </div>
</body>
</html>
```